Flyer für Verkauf von Radondetektoren
Zielgruppe
Ich verkaufe Radondetektoren zur Messung von Radon in Innenräumen. Zielgruppe sind Privatpersonen, Firmen, Genossenschaften und andere Hauseigentümer.
Aufgabenstellung
Ich brauche das Design für meine Messanleitung.
Kreativ - modern - weniger kann mehr sein
Struktur ist wichtigt, es soll also einfach sein zu lesen und zu verstehen, was gemacht werden soll. Können Bulletpoints, Icons mit eingebracht werden.
Wichtig ist auch, dass die beiden Logos 'Luftprüfer.de' und TESTOVAL' auf der Messanleitung vorhanden sind. Wobei 'Luftprüfer.de' das Hauptlogo ist.
DIN format dachte ich A4 beidseitig (Text müsste also auf diese Grösse angepasst werden).
Kann natürlich auch Flyer-Format sein oder andere Vorschläge!
Bildmaterial gibt es auf unsere Homepage https://luftprüfer.de und https://luftkontroll.se . Diese haben wir bereits gekauft und können verwendet werden. Ich lade sie den bei Bedarf hoch. Es können natürlich auch andere Vorschläge kommen.

```html
<!DOCTYPE html>
<html lang="de">
<head>
<meta charset="utf-8">
<title>Messanleitung – Luftprüfer.de</title>
<link href="https://fonts.googleapis.com/css2?family=Barlow:ital,wght@0,300;0,400;0,500;0,700;0,800;1,700&display=swap" rel="stylesheet">
<style>
  :root{
    --red:#e30613;
    --ink:#3c3c3b;
    --text:#4a4a49;
    --blue:#1f4e9a;
    --orange:#e8930c;
    --sky:#cfe6f5;
    --violet:#7f6bb1;
    --green:#5aa73a;
    --yellow:#fcd403;
  }
  *{box-sizing:border-box;margin:0;padding:0}
  html,body{width:1200px;height:848px;overflow:hidden;background:#fff}
  body{font-family:"Barlow",Arial,sans-serif;color:var(--text);position:relative}

  .step-bar{position:absolute;top:28px;height:61px;
    background:repeating-linear-gradient(135deg,#d9d9d9 0 3px,#cdcdcd 3px 5px);
    display:flex;align-items:center;padding-left:24px}
  .step-bar--3{left:0;width:318px}
  .step-bar--4{left:392px;width:330px}
  .step-num{font-weight:700;font-size:31px;color:var(--ink);margin-right:8px}
  .step-word{font-weight:500;font-size:19px;letter-spacing:1px;color:var(--ink);padding-top:6px}
  .step-badge{position:absolute;top:27px;width:63px;height:63px;border-radius:50%;
    background:var(--red);border:3px solid #fff;box-shadow:0 0 0 1px #ddd;
    display:flex;align-items:center;justify-content:center}
  .step-badge--3{left:302px}
  .step-badge--4{left:706px}

  .col{position:absolute}
  .col--1{left:24px;width:344px}
  .col--2{left:416px;width:356px}

  .heading{font-weight:700;font-size:27px;line-height:33px;color:var(--ink);letter-spacing:.3px}
  p.body{font-weight:300;font-size:14px;line-height:18.5px;text-align:justify;hyphens:auto;color:var(--text)}
  strong{font-weight:700;color:var(--ink)}

  .note{display:flex;align-items:center;gap:10px}
  .note-text{font-weight:700;font-style:italic;font-size:16px;line-height:21px;color:#1d1d1b}

  .mode{display:flex;align-items:center;gap:12px}
  .mode-title{font-weight:700;font-size:17px;color:var(--red);padding-top:10px}

  .bullets{list-style:none}
  .bullets li{font-weight:300;font-size:14px;line-height:18.5px;text-align:justify;hyphens:auto}
  .bullets li::before{content:"»";font-weight:500;font-size:18px;color:var(--ink);margin-right:8px;line-height:0}

  .address{display:flex;gap:14px;align-items:center}
  .address-lines{color:var(--red);font-size:14px;line-height:18.5px}
  .address-lines b{font-weight:700}

  .small-title{font-weight:700;font-style:italic;font-size:13px;color:var(--ink)}
  .small{font-weight:300;font-size:12.5px;line-height:15px;text-align:justify;hyphens:auto}

  .partner{position:absolute;left:418px;top:775px;display:flex;align-items:center;gap:10px}
  .partner-dot{width:34px;height:34px;border-radius:50%;background:var(--blue)}
  .partner-name{font-weight:500;font-size:38px;color:var(--blue);letter-spacing:.5px}

  .scene{position:absolute;left:796px;top:40px;width:404px;height:330px;
    background:linear-gradient(180deg,#fff 0%,var(--sky) 18%,var(--violet) 40%,var(--green) 72%,#8cbf3f 100%)}
  .cover-panel{position:absolute;left:796px;top:382px;width:404px;height:230px;
    background:
      linear-gradient(180deg,rgba(255,255,255,0) 0%,rgba(255,255,255,0) 45%,#fff 100%),
      repeating-linear-gradient(135deg,#dcdcdc 0 3px,#cfcfcf 3px 5px)}
  .cover-title{position:absolute;left:819px;top:402px;font-weight:800;font-size:42px;letter-spacing:2px;color:var(--ink)}
  .cover-sub{position:absolute;left:820px;top:451px;font-weight:500;font-size:22.5px;line-height:28.5px;color:var(--ink)}
  .product{position:absolute;left:965px;top:562px;width:215px;height:118px;border-radius:50%;
    background:radial-gradient(ellipse at 40% 35%,#5a5a5a 0%,#2b2b2b 55%,#111 100%)}

  .brand{position:absolute;left:826px;top:738px;display:flex;align-items:center;gap:12px}
  .brand-dot{width:40px;height:40px;border-radius:50%;background:var(--yellow)}
  .brand-name{font-weight:500;font-size:46px;color:#1d1d1b;line-height:46px}
  .brand-claim{position:absolute;left:884px;top:777px;width:284px;font-weight:500;font-size:14px;letter-spacing:.6px;color:var(--orange);white-space:nowrap}
  .cover-band{position:absolute;left:796px;top:832px;width:404px;height:16px;background:var(--red)}
</style>
</head>
<body>

  <div class="step-bar step-bar--3"><span class="step-num">3.</span><span class="step-word">SCHRITT</span></div>
  <div class="step-badge step-badge--3">
    <svg width="42" height="42" viewBox="0 0 42 42" fill="none" stroke="#fff" stroke-width="2.5">
      <circle cx="21" cy="23" r="15"/><path d="M21 8v15l9-7z" fill="#fff"/>
    </svg>
  </div>

  <section class="col col--1" style="top:142px">
    <h2 class="heading">RADONMESSUNG</h2>
    <p class="body" style="margin-top:11px">Die Radonmessung beginnt, sobald Sie die radondichten Verpackungen öffnen.</p>

    <div class="note" style="margin-top:21px">
      <svg width="46" height="44" viewBox="0 0 46 44" fill="none" stroke="var(--red)" stroke-width="4">
        <rect x="2" y="8" width="34" height="32" rx="4"/><path d="M10 22l9 9 23-28"/>
      </svg>
      <div class="note-text">Bitte halten Sie die Messdauer<br>wie folgt ein:</div>
    </div>

    <div class="mode" style="margin-top:30px">
      <svg width="42" height="42" viewBox="0 0 42 42" fill="none" stroke="var(--red)" stroke-width="2.2">
        <path d="M21 2A19 19 0 1 0 38 12"/><path d="M33 3l5 9-9 1"/><path d="M21 10v12l6 5"/>
      </svg>
      <span class="mode-title">Kurzzeitmessung</span>
    </div>
    <ul class="bullets" style="margin-top:16px">
      <li>Mindestmessdauer 10 Tage (bis hin zu 30 Tagen).</li>
      <li>Führen Sie die Messung vorzugsweise in der Heizperiode (1. Oktober – 30. April) durch.</li>
      <li>Kurzzeitmessungen werden oft beim Kauf oder Verkauf von Immobilien genutzt, um ein mögliches Gefährdungspotential abschätzen zu können, oder wenn die Zeit nicht ausreicht, um eine Langzeitmessung durchzuführen.</li>
    </ul>

    <div class="mode" style="margin-top:20px">
      <svg width="42" height="42" viewBox="0 0 42 42" fill="none" stroke="var(--red)" stroke-width="2.2">
        <path d="M21 2A19 19 0 1 1 4 12"/><path d="M9 3L4 12l9 1"/><path d="M21 10v12l-6 5"/>
      </svg>
      <span class="mode-title">Langzeitmessung</span>
    </div>
    <ul class="bullets" style="margin-top:16px">
      <li>Mindestmessdauer 3 Monate während der Heizperiode (1. Oktober – 30. April).</li>
      <li>Um einen Jahresmittelwert der Radonkonzentration in Innenräumen ermitteln zu können, halten Sie die Messdauer von 12 Monaten ein.</li>
      <li>Falls Ihr Arbeitsplatz in einem Radon-Vorsorgegebiet liegt und somit der Messpflicht unterliegt, muss die Messdauer von 12 Monaten eingehalten werden.</li>
    </ul>
  </section>

  <div class="step-bar step-bar--4"><span class="step-num">4.</span><span class="step-word">SCHRITT</span></div>
  <div class="step-badge step-badge--4">
    <svg width="38" height="34" viewBox="0 0 38 34" fill="#fff">
      <rect x="4" y="17" width="5" height="11"/><rect x="12" y="12" width="5" height="16"/>
      <rect x="20" y="14" width="5" height="14"/><rect x="28" y="5" width="5" height="23"/>
      <rect x="1" y="29" width="36" height="3"/>
    </svg>
  </div>

  <section class="col col--2" style="top:108px">
    <h2 class="heading">AUSWERTUNG<br>UND PRÜFBERICHT</h2>
    <p class="body" style="margin-top:17px">Nach Ablauf der Messdauer, loggen Sie sich wieder auf <strong>https://portal.testoval-labor.de</strong> in Ihrem Account ein. Vermerken Sie hier das Ende der Messung und senden Sie anschließend alle Radondetektoren ausreichend frankiert in einem Umschlag oder einem Karton zeitnah an unsere Rücksendeadresse:</p>

    <div class="address" style="margin-top:17px">
      <svg width="38" height="26" viewBox="0 0 38 26" fill="none" stroke="var(--red)" stroke-width="2.2">
        <rect x="1.5" y="1.5" width="35" height="23"/><path d="M1.5 1.5L19 15 36.5 1.5M1.5 24.5l13-12M36.5 24.5l-13-12"/>
      </svg>
      <div class="address-lines"><b>Luftprüfer.de</b><br>Ahornweg 7, 27612 Musterdorf</div>
    </div>

    <p class="body" style="margin-top:22px">Sobald die Radondetektoren im Labor von Testoval eingetroffen sind, werden diese fachgerecht analysiert und die Ergebnisse der Radonmessung ausgewertet. Ein vollständiger Prüfbericht wird Ihnen innerhalb 36 Stunden nach Erhalt der Detektoren im Labor per E-Mail zugeschickt.</p>

    <div class="small-title" style="margin-top:15px">Weitere Hinweise</div>
    <p class="small">• Bitte beachten Sie, dass die Radonmessung innerhalb von 15 Monaten nach Kaufdatum abgeschlossen sein muss.<br>
    • Versuchen Sie nicht das Gehäuse der Detektoren zu öffnen und platzieren Sie diese immer außer Reichweite von Kindern.<br>
    • Während der gesamten Messdauer dürfen die Detektoren nicht an einem anderen Ort umplatziert werden.<br>
    • Durch die Anmeldung auf der Website https://portal.testoval-labor.de und die Eingabe der erforderlichen Daten bestätigt der/die Wohnungseigentümer*in/Messverantwortliche, dass er/sie die Messanleitung befolgt hat und die Detektoren gemäß den Anweisungen korrekt platziert wurden.</p>

    <div class="small-title" style="margin-top:14px">Datenschutz (GDPR), Impressum und AGBs</div>
    <p class="small" style="text-align:left">Mehr Information dazu finden Sie unter www.luftprüfer.de<br>Copyright © 2023 Nordluft Mätteknik AB<br>Alle Rechte vorbehalten www.luftprüfer.de</p>
  </section>

  <div class="partner"><span class="partner-dot"></span><span class="partner-name">testoval</span></div>

  <div class="scene" role="img" aria-label="Illustration: Stadtsilhouette, grüne Hügel und Wohnhäuser unter blauem Himmel"></div>
  <div class="cover-panel"></div>
  <h1 class="cover-title">MESSANLEITUNG</h1>
  <div class="cover-sub">für Radonmessungen<br>von Innenraumluft<br>mit passiven Radon Detektoren</div>
  <div class="product" role="img" aria-label="Foto: zwei schwarze passive Radondetektoren"></div>

  <div class="brand"><span class="brand-dot"></span><span class="brand-name">Luftprüfer.de</span></div>
  <div class="brand-claim">IHR PARTNER FÜR GESUNDE RAUMLUFT</div>
  <div class="cover-band"></div>

</body>
</html>
```